Landscape design build company door flyer

I would like this flyer to convey a high-level of professionalism for a company that is excellent with communication with their clients as well as a company that does incredible installations

Went on vacation/holiday

```html
<!DOCTYPE html>
<html lang="en">
<head>
<meta charset="utf-8">
<title>Cedarline Builders – Outdoor Living Flyer</title>
<link href="https://fonts.googleapis.com/css2?family=Montserrat:wght@300;400;600;700;800&family=Outfit:wght@700&display=swap" rel="stylesheet">
<style>
  :root{
    --navy:#0f2a3d;
    --navy-deep:#0c2436;
    --teal-glow:#1d5a76;
    --paper:#ffffff;
    --backdrop:#e6e6e6;
    --rule-light:#b9bec3;
  }
  *{margin:0;padding:0;box-sizing:border-box}
  html,body{width:1200px;height:1029px;overflow:hidden;background:var(--backdrop)}
  body{font-family:"Montserrat",sans-serif;color:var(--navy);position:relative}

  .flyer{position:absolute;left:250px;top:64px;width:700px;height:900px;background:var(--paper);
    box-shadow:0 10px 30px rgba(0,0,0,.18)}

  .brand{position:absolute;left:0;top:55px;width:300px;text-align:center}
  .brand-mark{width:46px;height:46px;border-radius:50%;background:var(--navy);margin:0 auto 8px}
  .brand-name{font-family:"Montserrat",sans-serif;font-weight:700;font-size:15.5px;letter-spacing:.3px;color:var(--navy);line-height:1}
  .brand-tagline{font-weight:600;font-size:7px;letter-spacing:.2px;margin-top:3px;color:var(--navy)}

  .headline{position:absolute;left:35px;top:167px;font-family:"Outfit",sans-serif;font-weight:700;
    font-size:34px;line-height:33.5px;color:var(--navy);letter-spacing:-.2px}

  .divider{position:absolute;left:36px;top:317px;width:234px;height:1px;background:var(--rule-light)}
  .divider::before{content:"";position:absolute;left:0;top:-1px;width:113px;height:2.5px;background:var(--navy)}

  .intro{position:absolute;left:36px;top:333px;width:234px;font-weight:400;font-size:11.2px;line-height:13.4px;
    text-align:justify;color:var(--navy)}

  .services{position:absolute;left:36px;top:429px;list-style:none}
  .services li{height:31.2px;font-weight:700;font-size:14.6px;line-height:19px;padding-left:8px;
    border-left:2px solid var(--navy);height:19px;margin-bottom:12.2px;color:var(--navy)}

  .contact-panel{position:absolute;left:0;top:656px;width:300px;height:244px;
    background:radial-gradient(ellipse 160px 140px at 45% 68%,var(--teal-glow),var(--navy-deep) 100%);color:#fff}
  .service-areas{position:absolute;left:36px;top:13px;width:240px;font-weight:300;font-size:11.4px;line-height:16.8px}
  .service-areas strong{font-weight:600}
  .contact-tab{position:absolute;left:36px;top:98px}
  .contact-tab svg{display:block}
  .contact-label{position:absolute;left:6px;top:2px;font-weight:800;font-size:13.5px;letter-spacing:4.6px;color:var(--navy);line-height:16px}
  .phone{position:absolute;left:36px;top:131px;display:flex;align-items:center;gap:14px;font-weight:700;font-size:24.5px;letter-spacing:3.2px}
  .detail{position:absolute;left:40px;display:flex;align-items:center;gap:15px;font-weight:400;font-size:11.6px}
  .detail.email{top:164px}
  .detail.web{top:184px}

  .gallery{position:absolute;left:302px;top:0;width:398px;height:900px;display:flex;flex-direction:column;gap:3px}
  .photo{flex:1}
  .photo.firepit-lake{background:linear-gradient(180deg,#3d6fb3 0%,#2f5a93 28%,#1d2c38 42%,#6a7990 60%,#4c4c54 100%)}
  .photo.pergola-steps{background:linear-gradient(120deg,#5a4a3a 0%,#7b8c6a 35%,#4f7a2c 55%,#9a9c92 80%,#b9bbb4 100%)}
  .photo.pool-terrace{background:linear-gradient(160deg,#2d3a2c 0%,#4e5a63 35%,#5d6670 60%,#8a6a45 85%,#6a5a4c 100%)}
  .photo.wood-deck{background:linear-gradient(165deg,#5a6c4e 0%,#6b6058 22%,#b66a3c 45%,#d07e44 65%,#6a6a68 85%,#4a3a34 100%)}
</style>
</head>
<body>
<main class="flyer">
  <header class="brand">
    <div class="brand-mark"></div>
    <div class="brand-name">CEDARLINE BUILDERS</div>
    <div class="brand-tagline">OUTDOOR LIVING SPACES</div>
  </header>

  <h1 class="headline">LET’S CREATE<br>YOUR DREAM<br>OUTDOOR<br>LIVING SPACE!</h1>
  <div class="divider"></div>

  <p class="intro">Discover the endless possibilities for your outdoor space with The Cedarline Builders Team. Our team of skilled artisans is dedicated to turning your outdoor space into a breathtaking oasis that you’ll love coming home to. Our services include:</p>

  <ul class="services">
    <li>PAVER PATIOS</li>
    <li>PAVER DRIVEWAYS</li>
    <li>RETAINING WALLS</li>
    <li>DECKS &amp; RAILINGS</li>
    <li>POOLS</li>
    <li>OUTDOOR LIGHTING</li>
    <li>FIREPITS &amp; FIREPLACES</li>
  </ul>

  <section class="contact-panel">
    <p class="service-areas">Our service areas include <strong>Bellevue, Issaquah, Kirkland, Redmond, and Sammamish</strong>. We are trusted, tested and reliable with over 20-years experiences.</p>

    <div class="contact-tab">
      <svg width="228" height="20" viewBox="0 0 228 20">
        <path d="M0 0H150L155 10L150 20H0Z" fill="#fff"/>
        <line x1="155" y1="10" x2="227" y2="10" stroke="#c9d3da" stroke-width="1"/>
      </svg>
      <span class="contact-label">CONTACT US</span>
    </div>

    <div class="phone">
      <svg width="19" height="21" viewBox="0 0 24 24" aria-hidden="true"><path fill="#fff" d="M6.6 10.8c1.4 2.8 3.8 5.1 6.6 6.6l2.2-2.2c.3-.3.7-.4 1-.2 1.1.4 2.3.6 3.6.6.6 0 1 .4 1 1V20c0 .6-.4 1-1 1C10.6 21 3 13.4 3 4c0-.6.4-1 1-1h3.5c.6 0 1 .4 1 1 0 1.3.2 2.5.6 3.6.1.3 0 .7-.2 1z"/></svg>
      <span>206-555-0148</span>
    </div>
    <div class="detail email">
      <svg width="13" height="10" viewBox="0 0 13 10" aria-hidden="true"><rect width="13" height="10" fill="#fff"/><path d="M0 0L6.5 5.5L13 0" fill="none" stroke="#0f2a3d" stroke-width="1.3"/></svg>
      <span>info@cedarlinebuilders.com</span>
    </div>
    <div class="detail web">
      <svg width="13" height="13" viewBox="0 0 13 13" aria-hidden="true" fill="none" stroke="#fff" stroke-width=".9"><circle cx="6.5" cy="6.5" r="6"/><ellipse cx="6.5" cy="6.5" rx="2.6" ry="6"/><line x1=".5" y1="6.5" x2="12.5" y2="6.5"/></svg>
      <span>www.cedarlinebuilders.com</span>
    </div>
  </section>

  <div class="gallery">
    <div class="photo firepit-lake" role="img" aria-label="Lakeside patio at dusk with lounge chairs around a lit stone fire pit"></div>
    <div class="photo pergola-steps" role="img" aria-label="Backyard with curtained pergola, outdoor sofa, stone steps and retaining walls"></div>
    <div class="photo pool-terrace" role="img" aria-label="Evening paver terrace with curved lit seat walls, fire pit and swimming pool"></div>
    <div class="photo wood-deck" role="img" aria-label="Wet hardwood deck steps beside a stone patio"></div>
  </div>
</main>
</body>
</html>
```